Hollow Thicket, a 3d voxel survival video game needs a card for gaming conventions

I am the lead developer for Hollow Thicket http://www.HollowThicket.example and need a business card to hand out at an indie gaming convention
The card would need to include the game name, website url, my name, position (Lead Developer), e-mail and phone number
The game is a 3d, voxel (with smooth terrain) based survival game with guns and wildlife. The main icon of the game would likely be a grizzly bear but I am willing to accept other designs too.
Attached is a media kit for the game with some images you can use but don't have to its just what little art I can provide. Anything on the website or from the video game can also be used. unrelated art can also be used.
Target Market(s)
Indie Developers/publishers at conferences
Industry/Entity Type
Games
Contact Information for Business Card
Name: Corin Waldrick
Position: Lead Developer
E-mail: Pale_Kettle@mailbox.example
Phone number: 555-372-1186

```html
<!DOCTYPE html>
<html lang="en">
<head>
<meta charset="utf-8">
<title>Hollow Thicket – Business Card</title>
<link rel="stylesheet" href="https://fonts.googleapis.com/css2?family=Fira+Sans+Condensed:wght@500;600&family=Roboto:wght@400&display=swap">
<style>
  :root {
    --backdrop: #a4a2a3;
    --card-black: #1f1f20;
    --accent-red: #a31a17;
    --accent-tan: #8f8a6c;
    --logo-tan: #b4a77c;
    --text-white: #ffffff;
    --text-soft: #e6e6e6;
    --fur-light: #9a6f4a;
    --fur-dark: #4a2f1c;
    --rock: #c9c6c1;
  }
  * { margin: 0; padding: 0; box-sizing: border-box; }
  html, body { width: 1200px; height: 1200px; overflow: hidden; }
  body { background: var(--backdrop); position: relative; font-family: "Roboto", sans-serif; }

  .card {
    position: absolute;
    width: 715px;
    height: 421px;
    background: var(--card-black);
    overflow: hidden;
  }
  .card--front { left: 237px; top: 118px; }
  .card--back  { left: 229px; top: 643px; }

  /* Front */
  .front-emblem {
    position: absolute;
    left: 218px; top: 77px;
    width: 182px; height: 170px;
    border-radius: 46% 46% 10% 10%;
    background: radial-gradient(ellipse at 55% 40%, var(--fur-light), var(--fur-dark) 75%, var(--card-black));
  }
  .front-name {
    position: absolute;
    left: 0; width: 100%;
    top: 236px;
    text-align: center;
    font-family: "Fira Sans Condensed", sans-serif;
    font-weight: 600;
    font-size: 54px;
    line-height: 56px;
    letter-spacing: 3px;
    color: var(--logo-tan);
    text-transform: uppercase;
  }

  /* Back */
  .back-waves { position: absolute; inset: 0; width: 715px; height: 421px; }
  .back-title {
    position: absolute;
    right: 36px; top: 42px;
    font-family: "Fira Sans Condensed", sans-serif;
    font-weight: 600;
    font-size: 42px;
    letter-spacing: 2px;
    color: var(--logo-tan);
    text-transform: uppercase;
  }
  .person { position: absolute; right: 38px; top: 126px; text-align: right; }
  .person-name {
    font-family: "Fira Sans Condensed", sans-serif;
    font-weight: 500;
    font-size: 25px;
    color: var(--text-white);
  }
  .person-role { font-size: 16px; color: var(--text-soft); margin-top: 4px; }

  .back-photo {
    position: absolute;
    left: 0; top: 107px;
    width: 236px; height: 314px;
    border-radius: 40% 50% 0 0;
    background: linear-gradient(180deg, var(--fur-light) 0%, #7b5636 60%, var(--rock) 100%);
  }

  .contact { position: absolute; right: 33px; top: 308px; list-style: none; }
  .contact li {
    display: flex; align-items: center; justify-content: flex-end;
    height: 27px;
    font-size: 17px;
    color: var(--text-white);
  }
  .contact svg { width: 16px; height: 16px; margin-left: 12px; }
</style>
</head>
<body>

<section class="card card--front">
  <div class="front-emblem" role="img" aria-label="Photo of a roaring grizzly bear"></div>
  <div class="front-name">Hollow<br>Thicket</div>
</section>

<section class="card card--back">
  <svg class="back-waves" viewBox="0 0 715 421" aria-hidden="true">
    <path d="M0 330 C150 318 260 262 420 236 C560 214 650 206 715 200" fill="none" stroke="var(--accent-tan)" stroke-width="9"/>
    <path d="M0 372 C170 360 280 292 430 266 C560 246 650 236 715 232 L715 421 L0 421 Z" fill="var(--accent-red)"/>
    <path d="M0 356 C160 346 270 280 425 254 C560 232 650 224 715 220" fill="none" stroke="var(--card-black)" stroke-width="12"/>
  </svg>

  <div class="back-title">Hollow Thicket</div>

  <div class="person">
    <div class="person-name">Corin Waldrick</div>
    <div class="person-role">Lead Developer</div>
  </div>

  <div class="back-photo" role="img" aria-label="Photo of a grizzly bear standing on a rock"></div>

  <ul class="contact">
    <li>555-372-1186
      <svg viewBox="0 0 16 16"><path d="M2 5 Q8 1 14 5 L12 7 L10 6 L6 6 L4 7 Z M4 8 H12 L13 14 H3 Z" fill="var(--text-white)"/></svg>
    </li>
    <li>www.hollowthicket.example
      <svg viewBox="0 0 16 16"><rect x="1.5" y="3.5" width="13" height="9" fill="none" stroke="var(--text-white)" stroke-width="1.6"/><path d="M1.5 3.5 L8 9 L14.5 3.5" fill="none" stroke="var(--text-white)" stroke-width="1.6"/></svg>
    </li>
    <li>Pale_Kettle@mailbox.example
      <svg viewBox="0 0 16 16"><circle cx="8" cy="8" r="6.5" fill="none" stroke="var(--text-white)" stroke-width="1.4"/><ellipse cx="8" cy="8" rx="3" ry="6.5" fill="none" stroke="var(--text-white)" stroke-width="1.2"/><path d="M1.5 8 H14.5" stroke="var(--text-white)" stroke-width="1.2"/></svg>
    </li>
  </ul>
</section>

</body>
</html>
```